packaging design for disposable trash bag

We need 3 design for 3 of our products. first item is trash bag,the second item is disposable table cover and third is food packaging bag . We are a company in Singapore selling disposable product. This packaging products will be sold on shelf or online.

Attached is the requirement of the product. And some samples.

Target Market(s)

adult, most likely housewife

Requirements
Must have
• Packing design requirement for trash bag
• 1. Include company logo design, which is attached in the creative brief. DARVELLO POLYMER.
• 2. Clear showing of the product and its illustration of using. Eg. The trash bin.
• 3. Allocate a box for the purpose of sticking product size sticker.
• 4. Each packing bag holds 10pcs
• 5. Show of country of origin. Product of Singapore.
• 6. Use of one colour for printing of packing bag ( Black / blue/ bright Green/ white )
• 7. Show of warning: Keep polythene bags away from young children
• 8. dimension of the packagaing printing area : Lenght : 20 cm , Height 26 cm
• Packing design requirement for disposable Table Cover
• 1. Include company logo design, which is attached in the creative brief. Our company is DARVELLO POLYMER.
• 2. Clear showing of the product and its illustration of using. Eg. The table?.
• 4. Each packing bag holds 5pcs
• 6. Use of one colour for printing of the packing bag ( Black / blue/ bright Green )
• Packing design requirement for disposable food packaging plastic bag
• 2. Clear showing of the product and its illustration of using. Eg. Food?.
• 4. Show of country of origin. Product of Singapore.
• 5. Use of one colour for printing of the packing bag ( Black/ bright green )
• 6. Show of warning: Keep polythene bags away from young children
• 7. Show of product information: hygienic, food grade, freezer resistance, grease proof, damp proof, heat resistant.
• 8. Include the open here packing opening.
• 9. dimension of the packagaing printing area : Lenght : 15 cm , Height 22 cm
Nice to have
• requirement is stated in the must have. Good to allocate some space beside the packaging PCS area for promotion stickers . And also space allocated for bar code stickers.
Should not have
• no more than one color for printing

```html
<!DOCTYPE html>
<html lang="en">
<head>
<meta charset="utf-8">
<title>Disposable Table Cover – Pack Front</title>
<link href="https://fonts.googleapis.com/css2?family=Anton&family=Archivo+Black&family=Oswald:wght@500&family=Roboto+Condensed:wght@400;500;700&family=Roboto:wght@400;700;900&display=swap" rel="stylesheet">
<style>
  :root{
    --ink:#0a35a0;
    --film:#c7cee0;
    --film-light:#d3d9e8;
    --page:#eef0f5;
  }
  *{box-sizing:border-box;margin:0;padding:0}
  html,body{width:918px;height:1200px;overflow:hidden;background:var(--page)}
  .pack{position:relative;width:918px;height:1200px;background:var(--page);color:var(--ink);font-family:"Roboto",sans-serif}
  .print-area{position:absolute;left:60px;top:70px;width:798px;height:1060px;background:var(--film);border-radius:18px}
  .frame{position:absolute;left:100px;top:132px;width:716px;height:936px;border:3px solid var(--ink);border-radius:10px}
  .abs{position:absolute;white-space:nowrap}
  .bar{position:absolute;background:var(--ink)}
  .rule{position:absolute;background:var(--ink);height:3px}
  .vrule{position:absolute;background:var(--ink);width:3px}

  .qty-label{left:114px;top:177px;font-family:"Archivo Black",sans-serif;font-size:16px;line-height:17px;letter-spacing:.5px}
  .qty-value{left:238px;top:166px;font-family:"Anton",sans-serif;font-size:62px;line-height:76px;transform:scaleX(.92);transform-origin:left}
  .size-label{left:232px;top:240px;width:72px;text-align:center;background:var(--film);font-family:"Archivo Black",sans-serif;font-size:22px;line-height:28px}
  .sticker-box{position:absolute}
  .corner{position:absolute;width:30px;height:30px;border-color:var(--ink);border-style:solid;border-width:0}
  .corner.tl{left:0;top:0;border-left-width:3px;border-top-width:3px}
  .corner.tr{right:0;top:0;border-right-width:3px;border-top-width:3px}
  .corner.bl{left:0;bottom:0;border-left-width:3px;border-bottom-width:3px}
  .corner.br{right:0;bottom:0;border-right-width:3px;border-bottom-width:3px}
  .sticker-text{position:absolute;inset:0;display:flex;align-items:center;justify-content:center;font-weight:700;font-family:"Roboto",sans-serif}

  .title-top{left:478px;top:147px;width:312px;text-align:center;font-family:"Archivo Black",sans-serif;font-weight:400;font-size:41px;line-height:42px}
  .title-main{left:478px;width:312px;text-align:center;font-family:"Anton",sans-serif;font-size:112px;line-height:112px;transform:scaleX(1.26);transform-origin:center}

  .oxo{left:150px;top:478px;width:232px;text-align:center;font-family:"Oswald",sans-serif;font-weight:500;font-size:42px;line-height:44px;transform:scaleX(.58);transform-origin:center;letter-spacing:-.5px}
  .art{position:absolute;background:var(--film-light);border-radius:8px}
  .disposal-note{left:110px;top:698px;width:312px;text-align:center;font-family:"Roboto Condensed",sans-serif;font-weight:500;font-size:14.5px;line-height:18px}
  .hdpe{left:198px;top:810px;width:50px;text-align:center;font-size:10px;font-weight:700}
  .suitable{left:430px;top:696px;width:362px;text-align:center;font-family:"Roboto",sans-serif;font-weight:900;font-size:17px;letter-spacing:.3px}

  .origin{left:150px;top:860px;width:232px;text-align:center;font-family:"Roboto Condensed",sans-serif;font-size:17px}
  .brand{left:520px;top:862px;width:228px;text-align:center}
  .brand-mark{width:44px;height:50px;margin:0 auto 8px;background:var(--ink);border-radius:3px}
  .brand-name{font-family:"Roboto",sans-serif;font-size:21px;line-height:21px}
  .brand-web{font-family:"Roboto",sans-serif;font-weight:700;font-size:16px;margin-top:6px}
  .warning{left:116px;top:1024px;width:690px;font-family:"Roboto Condensed",sans-serif;font-weight:500;font-size:19px}
  .warning strong{font-family:"Archivo Black",sans-serif;font-weight:400;font-size:23px;letter-spacing:.5px}
</style>
</head>
<body>
<main class="pack">
  <div class="print-area"></div>
  <div class="frame"></div>

  <div class="bar" style="left:100px;top:148px;width:334px;height:15px"></div>
  <div class="vrule" style="left:431px;top:148px;height:274px"></div>
  <div class="rule" style="left:100px;top:236px;width:334px"></div>
  <p class="abs qty-label">CONTENT<br>QUANTITY</p>
  <p class="abs qty-value">5 PIECES</p>
  <div class="bar" style="left:100px;top:246px;width:334px;height:15px"></div>
  <p class="abs size-label">SIZE</p>
  <div class="sticker-box" style="left:108px;top:270px;width:314px;height:134px">
    <span class="corner tl"></span><span class="corner tr"></span>
    <span class="corner bl"></span><span class="corner br"></span>
    <span class="sticker-text" style="font-size:20px">SIZE (DIMENSION)</span>
  </div>

  <h1 class="abs title-top">DISPOSABLE</h1>
  <p class="abs title-main" style="top:184px">TABLE</p>
  <p class="abs title-main" style="top:298px">COVER</p>

  <div class="bar" style="left:100px;top:414px;width:716px;height:18px"></div>

  <p class="abs oxo">OXO-BIODEGRADABLE</p>
  <div class="art" style="left:192px;top:532px;width:152px;height:108px" role="img" aria-label="Go green emblem with leaves and curved arrow"></div>
  <p class="abs disposal-note">USED BAGS SHOULD BE TIED PROPERLY<br>BEFORE DISPOSAL TO ENSURE CLEANLINESS<br>TO THE SURROUNDING ENVIRONMENT.</p>
  <div class="art" style="left:200px;top:766px;width:136px;height:42px" role="img" aria-label="HDPE recycling, recycle and tidy disposal icons"></div>
  <p class="abs hdpe">HDPE</p>

  <div class="art" style="left:432px;top:544px;width:368px;height:124px" role="img" aria-label="Square table and round table silhouettes"></div>
  <p class="abs suitable">SUITABLE FOR ALL TYPES TABLES</p>

  <div class="rule" style="left:100px;top:837px;width:716px"></div>
  <div class="bar" style="left:432px;top:836px;width:384px;height:16px"></div>
  <p class="abs origin">PRODUCT OF SINGAPORE</p>
  <div class="sticker-box" style="left:170px;top:894px;width:195px;height:88px">
    <span class="corner tl" style="width:24px;height:24px"></span><span class="corner tr" style="width:24px;height:24px"></span>
    <span class="corner bl" style="width:24px;height:24px"></span><span class="corner br" style="width:24px;height:24px"></span>
    <span class="sticker-text" style="font-size:18px">BARCODE</span>
  </div>
  <div class="abs brand">
    <div class="brand-mark"></div>
    <p class="brand-name">DARVELLO POLYMER<br>PTE LTD</p>
    <p class="brand-web">www.darvellopolymer.com</p>
  </div>
  <div class="bar" style="left:432px;top:992px;width:384px;height:16px"></div>
  <div class="rule" style="left:100px;top:1006px;width:716px"></div>

  <p class="abs warning"><strong>WARNING:</strong> PLEASE KEEP POLYTHENE BAGS AWAY FROM YOUNG CHILDREN</p>
</main>
</body>
</html>
```